Tidal Forge - Crypto Currency Miner Powered by Renewable Energy Website

We Need Web Pages Design for Website for Crypto Currency Miner

Serivices include:
Mining Rig Sales
Housing for Rigs turnkey on renewable energy grid
Cloud Mining term packages
Updates

http://www.vaultrigsurvey.example (Competitors sites)

Target Market(s)

Investers for Mining Rigs and terms for 1,2 or 3 years of Hash rate

Industry/Entity Type

Mining

Number of Pages Required

5+ page

Font styles to use
Sans Serif

Colors
add136
9bcb3c
606060
474747
ffc214
cadf82
fbee3e
876aae
6b449b

Requirements
Must have
• Pictures of Solar, Wind and power Factor Correction units
Nice to have
• e-commerce platform so contract terms can be purchased through website
Should not have
• Heavy construction equipment

```html
<!DOCTYPE html>
<html lang="en">
<head>
<meta charset="utf-8">
<title>Tidal Forge – Crypto Currency Miner</title>
<link href="https://fonts.googleapis.com/css2?family=Roboto:wght@400;500;700;900&display=swap" rel="stylesheet">
<style>
:root{
  --green:#3fae2a;
  --green-light:#9bcb3c;
  --green-dark:#2f8f1f;
  --text:#606060;
  --heading:#2b2b2b;
  --nav:#474747;
  --yellow:#ffc214;
  --red:#e0151f;
  --footer:#1f1f1f;
  --footer-bottom:#141414;
  --white:#ffffff;
  --muted:#9a9a9a;
}
*{box-sizing:border-box;margin:0;padding:0}
html,body{width:1200px;height:3780px;overflow:hidden}
body{font-family:"Roboto",Arial,sans-serif;color:var(--text);background:var(--white);position:relative}
section,header,footer{position:absolute;left:0;width:1200px}
p{font-size:13px;line-height:20px}

/* Header */
.site-header{top:0;height:128px;background:var(--white)}
.brand{position:absolute;left:100px;top:34px;display:flex;align-items:center;gap:12px}
.brand-dot{width:44px;height:44px;border-radius:50%;background:var(--green)}
.brand-name{font-size:30px;font-weight:700;color:var(--green)}
.topbar{position:absolute;right:100px;top:22px;display:flex;align-items:center;gap:22px}
.call{display:flex;align-items:center;gap:8px;font-size:15px;color:var(--nav);font-weight:500}
.btn{display:inline-block;font-size:11px;font-weight:700;letter-spacing:.5px;text-transform:uppercase;color:var(--white);background:var(--green);padding:9px 18px}
.main-nav{position:absolute;right:100px;top:82px;display:flex;gap:30px}
.main-nav a{font-size:14px;font-weight:700;color:var(--nav);text-decoration:none;padding-bottom:6px}
.main-nav a.active{color:var(--green);border-bottom:2px solid var(--green)}

/* Hero */
.hero{top:128px;height:532px}
.hero-photo{position:absolute;inset:0;background:linear-gradient(180deg,#8fb3cf 0%,#c9d9e3 45%,#7fa05a 62%,#3f6a2c 80%,#2d4a5c 100%)}
.hero-copy{position:absolute;left:720px;top:200px;width:380px;color:var(--white)}
.hero-copy h1{font-size:46px;font-weight:900;line-height:50px;margin-bottom:14px}
.hero-copy p{color:#f0f0f0;margin-bottom:18px}
.slider-arrow{position:absolute;top:246px;width:34px;height:40px;background:rgba(0,0,0,.45);display:flex;align-items:center;justify-content:center}
.slider-arrow.prev{left:20px}
.slider-arrow.next{right:20px}

/* Features */
.features{top:660px;height:500px}
.feature{position:absolute;width:420px;display:flex;gap:22px}
.feature-icon{flex:none;width:78px;height:78px;border-radius:50%;background:var(--green);border:5px solid #d9eecf;display:flex;align-items:center;justify-content:center}
.feature h3{font-size:20px;font-weight:500;color:var(--heading);margin:8px 0 10px}

/* Welcome */
.welcome{top:1160px;height:620px}
.welcome-photo{position:absolute;left:0;top:0;width:600px;height:620px;background:radial-gradient(circle at 55% 45%,#5fa8e0 0%,#1b4f9a 35%,#0b1a3c 80%);clip-path:polygon(0 90px,600px 0,600px 620px,0 580px)}
.welcome-panel{position:absolute;left:600px;top:0;width:600px;height:620px;background:var(--green);clip-path:polygon(0 0,600px 90px,600px 560px,0 620px);color:var(--white);padding:150px 100px 0 60px}
.welcome-panel h2{font-size:38px;font-weight:900;line-height:42px;margin-bottom:22px}
.welcome-panel p{color:#eaf6e4;margin-bottom:14px}
.btn-outline{display:inline-block;margin-top:10px;font-size:11px;font-weight:700;color:var(--white);border:2px solid var(--white);padding:8px 16px}

/* Miner */
.miner{top:1780px;height:520px}
.section-title{text-align:center;font-size:32px;font-weight:700;color:var(--heading);text-transform:uppercase}
.miner .section-title{position:absolute;top:40px;width:100%}
.miner-frame{position:absolute;left:92px;top:130px;width:468px;height:320px;background:var(--green)}
.miner-photo{position:absolute;left:104px;top:142px;width:460px;height:320px;background:linear-gradient(135deg,#cfd6dc 0%,#8797a6 45%,#3b5068 100%)}
.miner-list{position:absolute;left:620px;top:140px;width:480px}
.miner-item{display:flex;gap:18px;margin-bottom:26px}
.miner-item svg{flex:none}
.miner-item h4{font-size:16px;font-weight:700;color:var(--heading);text-transform:uppercase;margin:2px 0 6px}

/* Monitoring */
.monitoring{top:2300px;height:660px;background:linear-gradient(180deg,#c8101a 0%,var(--red) 100%);text-align:center;color:var(--white)}
.monitoring h2{margin-top:70px;font-size:38px;font-weight:900}
.monitoring .lead{font-size:16px;margin-top:8px;color:#ffe4e4}
.dashboard-device{position:absolute;left:330px;top:180px;width:540px;height:390px;border-radius:12px;background:linear-gradient(180deg,#2a2a2a 0%,#2a2a2a 6%,#f1f3f5 6%,#dfe4e8 92%,#b9bec4 92%,#8c9196 100%)}

/* Blog */
.blog{top:2960px;height:540px}
.blog .section-title{position:absolute;top:60px;width:100%}
.blog-card{position:absolute;top:150px;width:310px}
.blog-photo{position:relative;height:190px}
.date-badge{position:absolute;right:14px;top:0;width:52px;height:70px;background:var(--yellow);color:var(--heading);text-align:center;font-size:11px;font-weight:700;line-height:14px;padding-top:9px}
.date-badge strong{display:block;font-size:20px;line-height:22px}
.blog-card h3{font-size:16px;font-weight:700;color:var(--heading);margin:20px 0 8px}

/* Footer */
.site-footer{top:3500px;height:280px;background:var(--footer);color:#cfcfcf}
.footer-col{position:absolute;top:32px}
.footer-col h4{font-size:15px;font-weight:700;color:var(--white);text-transform:uppercase;margin-bottom:16px}
.footer-col p,.footer-col li{font-size:12px;line-height:19px;color:#bdbdbd}
.footer-col ul{list-style:none}
.contact-line{display:flex;gap:10px;align-items:flex-start;margin-bottom:8px}
.signup-input{width:260px;height:30px;background:var(--white);margin:12px 0 10px;font-size:11px;color:var(--muted);padding:8px 10px}
.btn-subscribe{display:inline-block;background:var(--yellow);color:var(--heading);font-size:11px;font-weight:700;padding:8px 16px}
.social li{display:flex;align-items:center;gap:8px;margin-bottom:4px}
.social-dot{width:14px;height:14px;border-radius:50%;background:#4a4a4a}
.copyright{position:absolute;left:0;bottom:0;width:100%;height:44px;background:var(--footer-bottom);text-align:center;font-size:11px;line-height:44px;color:var(--muted)}
.to-top{position:absolute;right:30px;bottom:10px;width:24px;height:24px;background:#333}
</style>
</head>
<body>

<header class="site-header">
  <div class="brand"><span class="brand-dot"></span><span class="brand-name">Tidal Forge</span></div>
  <div class="topbar">
    <span class="call">
      <svg width="16" height="16" viewBox="0 0 24 24"><path fill="#3fae2a" d="M6.6 10.8a15 15 0 0 0 6.6 6.6l2.2-2.2a1 1 0 0 1 1-.25 11.4 11.4 0 0 0 3.6.57 1 1 0 0 1 1 1V20a1 1 0 0 1-1 1A17 17 0 0 1 3 4a1 1 0 0 1 1-1h3.5a1 1 0 0 1 1 1c0 1.25.2 2.450.57 3.57a1 1 0 0 1-.25 1z"/></svg>
      Call Us : 800 555 0147
    </span>
    <span class="btn">Request a free estimate</span>
  </div>
  <nav class="main-nav">
    <a class="active" href="#">HOME</a>
    <a href="#">ABOUT US</a>
    <a href="#">OUR SERVICES</a>
    <a href="#">PROJECTS</a>
    <a href="#">BLOG</a>
    <a href="#">CONTACT US</a>
  </nav>
</header>

<section class="hero">
  <div class="hero-photo" role="img" aria-label="Wind turbines standing over a field of solar panels under a blue sky"></div>
  <div class="slider-arrow prev"><svg width="12" height="16" viewBox="0 0 12 16"><path d="M9 2 3 8l6 6" stroke="#fff" stroke-width="2.5" fill="none"/></svg></div>
  <div class="slider-arrow next"><svg width="12" height="16" viewBox="0 0 12 16"><path d="m3 2 6 6-6 6" stroke="#fff" stroke-width="2.5" fill="none"/></svg></div>
  <div class="hero-copy">
    <h1>THE TIDAL<br>FORGE</h1>
    <p>Sed ut perspiciatis unde omnis iste natus error sit voluptatem accusantium doloremque laudantium, totam rem aperiam, eaque ipsa quae.</p>
    <span class="btn">Read more</span>
  </div>
</section>

<section class="features">
  <div class="feature" style="left:100px;top:110px">
    <div class="feature-icon"><svg width="34" height="34" viewBox="0 0 34 34"><rect x="5" y="7" width="24" height="18" rx="2" stroke="#fff" stroke-width="2.5" fill="none"/><path d="M12 30h10M17 25v5" stroke="#fff" stroke-width="2.5"/></svg></div>
    <div><h3>Crypto Currency Miner</h3><p>Sed ut perspiciatis unde omnis iste natus error sit voluptatem accusantium doloremque laudantium, totam rem aperiam, eaque ipsa quae ab illo inventore veritatis et quasi architecto beatae vitae dicta sunt explicabo.</p></div>
  </div>
  <div class="feature" style="left:640px;top:110px">
    <div class="feature-icon"><svg width="34" height="34" viewBox="0 0 34 34"><path d="M5 12h22l-5-5M29 22H7l5 5" stroke="#fff" stroke-width="2.5" fill="none"/></svg></div>
    <div><h3>Bitcoin Transaction</h3><p>Sed ut perspiciatis unde omnis iste natus error sit voluptatem accusantium doloremque laudantium, totam rem aperiam, eaque ipsa quae ab illo inventore veritatis et quasi architecto beatae vitae dicta sunt explicabo.</p></div>
  </div>
  <div class="feature" style="left:100px;top:300px">
    <div class="feature-icon"><svg width="34" height="34" viewBox="0 0 34 34"><circle cx="17" cy="17" r="12" stroke="#fff" stroke-width="2.5" fill="none"/><path d="M11 15h12l-3-3M23 20H11l3 3" stroke="#fff" stroke-width="2" fill="none"/></svg></div>
    <div><h3>Bitcoin Exchange</h3><p>Sed ut perspiciatis unde omnis iste natus error sit voluptatem accusantium doloremque laudantium, totam rem aperiam, eaque ipsa quae ab illo inventore veritatis et quasi architecto beatae vitae dicta sunt explicabo.</p></div>
  </div>
  <div class="feature" style="left:640px;top:300px">
    <div class="feature-icon"><svg width="34" height="34" viewBox="0 0 34 34"><circle cx="17" cy="17" r="12" stroke="#fff" stroke-width="2.5" fill="none"/><path d="M17 9v9l6 4" stroke="#fff" stroke-width="2.5" fill="none"/></svg></div>
    <div><h3>Instant Withdrawal</h3><p>Sed ut perspiciatis unde omnis iste natus error sit voluptatem accusantium doloremque laudantium, totam rem aperiam, eaque ipsa quae ab illo inventore veritatis et quasi architecto beatae vitae dicta sunt explicabo.</p></div>
  </div>
</section>

<section class="welcome">
  <div class="welcome-photo" role="img" aria-label="Businessman holding a glowing digital coin over a blue network background"></div>
  <div class="welcome-panel">
    <h2>WELCOME TO<br>THE TIDAL FORGE</h2>
    <p>Sed ut perspiciatis unde omnis iste natus error sit voluptatem accusantium doloremque laudantium, totam rem aperiam, eaque ipsa quae ab illo inventore veritatis et quasi architecto beatae vitae dicta sunt explicabo. Nemo enim ipsam voluptatem quia voluptas sit aspernatur aut odit aut fugit.</p>
    <p>Sed ut perspiciatis unde omnis iste natus error sit voluptatem accusantium doloremque laudantium, totam rem aperiam, eaque ipsa quae ab illo inventore veritatis et quasi architecto beatae vitae dicta sunt explicabo.</p>
    <span class="btn-outline">READ MORE</span>
  </div>
</section>

<section class="miner">
  <h2 class="section-title">Crypto Currency Miner</h2>
  <div class="miner-frame"></div>
  <div class="miner-photo" role="img" aria-label="Miner in a hard hat holding up a gold coin"></div>
  <div class="miner-list">
    <div class="miner-item">
      <svg width="40" height="40" viewBox="0 0 40 40"><rect x="8" y="12" width="24" height="20" rx="3" fill="#3fae2a"/><circle cx="15" cy="21" r="2.5" fill="#fff"/><circle cx="25" cy="21" r="2.5" fill="#fff"/><path d="M20 12V6" stroke="#3fae2a" stroke-width="2.5"/></svg>
      <div><h4>Performing Trading Bots</h4><p>Sed ut perspiciatis unde omnis iste natus error sit voluptatem accusantium doloremque laudantium, totam rem aperiam, eaque ipsa quae ab illo inventore veritatis et quasi.</p></div>
    </div>
    <div class="miner-item">
      <svg width="40" height="40" viewBox="0 0 40 40"><circle cx="22" cy="14" r="8" fill="#3fae2a"/><path d="M4 30h8l8 4 14-8-3-3-11 5" stroke="#3fae2a" stroke-width="3" fill="none"/></svg>
      <div><h4>Simple Remuneration Scheme</h4><p>Sed ut perspiciatis unde omnis iste natus error sit voluptatem accusantium doloremque laudantium, totam rem aperiam, eaque ipsa quae ab illo inventore veritatis et quasi.</p></div>
    </div>
    <div class="miner-item">
      <svg width="40" height="40" viewBox="0 0 40 40"><rect x="6" y="24" width="6" height="10" fill="#3fae2a"/><rect x="16" y="18" width="6" height="16" fill="#3fae2a"/><rect x="26" y="10" width="6" height="24" fill="#3fae2a"/></svg>
      <div><h4>Scalable Business Model</h4><p>Sed ut perspiciatis unde omnis iste natus error sit voluptatem accusantium doloremque laudantium, totam rem aperiam, eaque ipsa quae ab illo inventore veritatis et quasi.</p></div>
    </div>
  </div>
</section>

<section class="monitoring">
  <h2>REAL-TIME MINING MONITORING</h2>
  <p class="lead">Sed ut perspiciatis unde omnis iste natus.</p>
  <div class="dashboard-device" role="img" aria-label="Laptop showing a mining monitoring dashboard"></div>
</section>

<section class="blog">
  <h2 class="section-title">Latest Blog</h2>
  <article class="blog-card" style="left:100px">
    <div class="blog-photo" role="img" aria-label="Stacks of gold coins beside a mining rig" style="background:linear-gradient(135deg,#2c3440 0%,#8a6a2a 60%,#d2a63c 100%)">
      <div class="date-badge"><strong>29</strong>MAY<br>2018</div>
    </div>
    <h3>Nemo enim ipsam voluptatem</h3>
    <p>Sed ut perspiciatis unde omnis iste natus error sit voluptatem accusantium doloremque laudantium, totam rem aperiam.</p>
  </article>
  <article class="blog-card" style="left:445px">
    <div class="blog-photo" role="img" aria-label="Blue digital currency graphic over a circuit background" style="background:linear-gradient(135deg,#0d2c5a 0%,#1f6fb8 55%,#7cc3ef 100%)">
      <div class="date-badge"><strong>29</strong>MAY<br>2018</div>
    </div>
    <h3>Nemo enim ipsam voluptatem</h3>
    <p>Sed ut perspiciatis unde omnis iste natus error sit voluptatem accusantium doloremque laudantium, totam rem aperiam.</p>
  </article>
  <article class="blog-card" style="left:790px">
    <div class="blog-photo" role="img" aria-label="Crypto currency headline graphic on a purple background" style="background:linear-gradient(135deg,#3a1f5c 0%,#6b449b 55%,#876aae 100%)">
      <div class="date-badge"><strong>29</strong>MAY<br>2018</div>
    </div>
    <h3>Nemo enim ipsam voluptatem</h3>
    <p>Sed ut perspiciatis unde omnis iste natus error sit voluptatem accusantium doloremque laudantium, totam rem aperiam.</p>
  </article>
</section>

<footer class="site-footer">
  <div class="footer-col" style="left:100px;width:280px">
    <h4>Contact Us</h4>
    <div class="contact-line"><svg width="12" height="14" viewBox="0 0 12 14"><path d="M6 0a5 5 0 0 0-5 5c0 4 5 9 5 9s5-5 5-9a5 5 0 0 0-5-5z" fill="#3fae2a"/></svg><p>127 Harbour Lane,<br>Northport NP4 2QT</p></div>
    <div class="contact-line"><svg width="12" height="12" viewBox="0 0 24 24"><path fill="#3fae2a" d="M6.6 10.8a15 15 0 0 0 6.6 6.6l2.2-2.2a1 1 0 0 1 1-.25 11.4 11.4 0 0 0 3.6.57 1 1 0 0 1 1 1V20a1 1 0 0 1-1 1A17 17 0 0 1 3 4a1 1 0 0 1 1-1h3.5a1 1 0 0 1 1 1c0 1.25.2 2.45.57 3.57a1 1 0 0 1-.25 1z"/></svg><p>Phone : +44 (0)20 5550 1234</p></div>
    <div class="contact-line"><svg width="12" height="10" viewBox="0 0 12 10"><rect x=".5" y=".5" width="11" height="9" fill="none" stroke="#3fae2a"/><path d="m.5.5 5.5 5 5.5-5" fill="none" stroke="#3fae2a"/></svg><p>Mail : hello@tidalforge.example</p></div>
  </div>
  <div class="footer-col" style="left:430px;width:300px">
    <h4>Sign up to receive email</h4>
    <p>Sed ut perspiciatis unde omnis iste natus error sit voluptatem accusantium doloremque laudantium, totam rem aperiam.</p>
    <div class="signup-input">Enter Email</div>
    <span class="btn-subscribe">SUBSCRIBE</span>
  </div>
  <div class="footer-col" style="left:800px;width:140px">
    <h4>Quick Links</h4>
    <ul><li>Home</li><li>About Us</li><li>Services</li><li>Blog</li><li>Who we are</li><li>Contact Us</li></ul>
  </div>
  <div class="footer-col social" style="left:960px;width:140px">
    <h4>Social</h4>
    <ul>
      <li><span class="social-dot"></span>Kinlink</li>
      <li><span class="social-dot"></span>Chirpline</li>
      <li><span class="social-dot"></span>Searchplus</li>
      <li><span class="social-dot"></span>Workweb</li>
    </ul>
  </div>
  <div class="copyright">Copyright © The Tidal Forge 2018. All rights reserved.</div>
  <div class="to-top"><svg width="24" height="24" viewBox="0 0 24 24"><path d="m7 14 5-5 5 5" stroke="#fff" stroke-width="2" fill="none"/></svg></div>
</footer>

</body>
</html>
```